Logo & Visitenkarte für Schreinermonteur (Fenster und Türen)
Sehr gute Designerin, gute Ideen und sie hat alle Änderungswünsche sehr schnell und genau umgesetzt. Jederzeit gerne wieder!
Zielgruppe
Verkauf und Einbau von Fenster und Türen (Bauelemente). Meine Zielgruppen sind Menschen, die ein Haus bauen oder renovieren und Fenster und Türen benötigen. Ich mache die Berautung und baue anschliessend die Türen, Fenster und Jalousien auch mit meinem Team ein.
Aufgabenstellung
Ich bin selbständiger Schreiner im Südschwarzwald und derzeit auf den Einbau von Fenster und Türen spezialisiert. Ich möchte meine Initialien RM in meinem Logo enthalten haben, bin aber auch offen für andere Vorschläge. Derzeit bin ich unter 'RM Tischlermontagen' bekannt.
Gerne darf als Untertitel 'Fenster und Türen' verwendet werden. Da ich die Option haben möchte, dass ich das Logo/meine Initialien weiterverwende, aber meine Spezialisierung von 'Fenster und Türen' ändere, sollte dies zwar im Logo enthalten sein, aber nicht zu stark integriert sein.
Ich arbeite in einer ländlichen Gegend und das Logo sollte Zuverlässigkeit, Flexibilität und Individualität ausstrahlen und einen hohen Widererkennungswert haben, da es viele andere Schreiner hier gibt. Ich bin bekannt für meine exakte und qualitativ hochwertige Arbeit und bin auch ein Spezialist, wenn es um die Beratung meiner Kunden bei der Fenster und Türenauswahl geht.
Bei den Farben bin ich noch etwas unentschlossen. Derzeit habe ich grau-blau als Farben, bin aber offen für andere Vorschläge. Nur bitte kein rot/rosa. Falls Fragen sind, bitte einfach kurz schreiben.
Besten Dank vorab für die Vorschläge!

```html
<!DOCTYPE html>
<html lang="de">
<head>
<meta charset="utf-8">
<title>R. Mertens – Visitenkarten</title>
<link href="https://fonts.googleapis.com/css2?family=Roboto:wght@400;500;700&family=Roboto+Condensed:wght@700&display=swap" rel="stylesheet">
<style>
  :root {
    --stage: #00131c;
    --card: #ffffff;
    --navy: #0b0b6e;
    --ink: #1f1f1f;
    --rule: #8a8a8a;
  }
  * { margin: 0; padding: 0; box-sizing: border-box; }
  html, body { width: 1200px; height: 818px; overflow: hidden; background: var(--stage); }
  body { position: relative; font-family: "Roboto", Arial, sans-serif; }

  .card {
    position: absolute;
    width: 469px; height: 287px;
    background: var(--card);
    overflow: hidden;
  }
  .card--front-a { left: 125px; top: 87px; }
  .card--back    { left: 605px; top: 87px; }
  .card--front-b { left: 123px; top: 443px; }
  .card--front-c { left: 605px; top: 443px; }

  .band { position: absolute; display: block; }

  .wordmark {
    position: absolute;
    color: var(--navy);
    font-weight: 700;
    letter-spacing: -0.5px;
    white-space: nowrap;
  }

  /* Front A */
  .card--front-a .wordmark { left: 0; right: 0; top: 104px; text-align: center; font-size: 50px; line-height: 1; }
  .tagline-condensed {
    position: absolute; left: 0; right: 0; top: 255px;
    text-align: center;
    font-family: "Roboto Condensed", "Arial Narrow", sans-serif;
    font-weight: 700; font-size: 13.5px; color: var(--navy);
    letter-spacing: 0.1px;
  }

  /* Back */
  .monogram {
    position: absolute; left: 30px; top: 92px;
    font-size: 100px; font-weight: 700; line-height: 1;
    color: var(--navy); letter-spacing: -4px;
  }
  .divider { position: absolute; left: 220px; top: 72px; width: 1px; height: 142px; background: var(--rule); }
  .contact { position: absolute; left: 257px; top: 65px; color: var(--ink); font-size: 13px; line-height: 15.5px; }
  .contact__name { font-size: 23px; font-weight: 700; color: var(--navy); line-height: 28px; margin-bottom: 3px; }
  .contact__block { margin-bottom: 14px; }
  .contact__block:last-child { margin-bottom: 0; }
  .contact__row { display: flex; }
  .contact__label { width: 44px; font-weight: 700; }
  .contact__block--web { margin-top: -10px; }

  /* Front B */
  .card--front-b .wordmark { left: 22px; top: 38px; font-size: 42px; line-height: 1; }
  .services {
    position: absolute; right: 8px; top: 138px;
    list-style: none; text-align: right;
    color: var(--navy); font-weight: 700; font-size: 17.5px; line-height: 26px;
  }

  /* Front C */
  .card--front-c .wordmark { left: 0; right: 0; top: 124px; text-align: center; font-size: 28px; line-height: 1; }
  .footer-bar {
    position: absolute; left: 0; right: 0; bottom: 0; height: 29px;
    background: var(--navy); color: #fff;
    font-size: 9.5px; font-weight: 700; letter-spacing: 0.4px;
    display: flex; align-items: center; justify-content: center;
  }
</style>
</head>
<body>

  <section class="card card--front-a">
    <div class="wordmark">R. Mertens</div>
    <p class="tagline-condensed">FENSTER | TÜREN | ROLLLÄDEN | RAFFSTOREN | INSEKTENSCHUTZ</p>
  </section>

  <section class="card card--back">
    <svg class="band" width="469" height="287" viewBox="0 0 469 287" aria-hidden="true">
      <polygon points="0,0 220,0 196,17 0,17" fill="var(--navy)"/>
      <polygon points="273,270 469,270 469,287 249,287" fill="var(--navy)"/>
    </svg>
    <div class="monogram">RM</div>
    <div class="divider"></div>
    <div class="contact">
      <div class="contact__name">Rainer Mertens</div>
      <div class="contact__block">
        Lindenweg 12<br>
        79787 Tannbach-Oberhof
      </div>
      <div class="contact__block">
        <div class="contact__row"><span class="contact__label">Mobil</span>: 0170 555 18 27</div>
        <div class="contact__row"><span class="contact__label">Büro</span>: 07741 555 62 90</div>
        <div class="contact__row"><span class="contact__label">Fax</span>: 03212 555 40 71</div>
      </div>
      <div class="contact__block contact__block--web">
        mertens@mail-muster.de<br>
        www.rainer-mertens-muster.de
      </div>
    </div>
  </section>

  <section class="card card--front-b">
    <div class="wordmark">R. Mertens</div>
    <ul class="services">
      <li>FENSTER</li>
      <li>TÜREN</li>
      <li>ROLLLÄDEN</li>
      <li>RAFFSTOREN</li>
      <li>INSEKTENSCHUTZ</li>
    </ul>
    <svg class="band" style="left:0;top:0" width="469" height="287" viewBox="0 0 469 287" aria-hidden="true">
      <polygon points="200,270 469,270 469,287 168,287" fill="var(--navy)"/>
    </svg>
  </section>

  <section class="card card--front-c">
    <svg class="band" width="469" height="11" viewBox="0 0 469 11" aria-hidden="true">
      <rect width="469" height="11" fill="var(--navy)"/>
    </svg>
    <div class="wordmark">R. Mertens</div>
    <div class="footer-bar">FENSTER | TÜREN | ROLLLÄDEN | RAFFSTOREN | INSEKTENSCHUTZ</div>
  </section>

</body>
</html>
```